Foot doctor needs feet friendly business cards.

Business cards for Podiatrist. Needs to look professional and modern. Back side put an appointment card, and try to put a little basic street map somewhere on card along with all of our contact info below:

Marcus Dovan, DPM, Inc.
Diplomate, National Council of Lower Limb Medicine
Call: 1.877.Toes.482
1.555.283.9146
Fax: 1.555.671.3820
Email: info@DrDovanclinic.example
Web: www.DrDovanclinic.example
2847 W. Harbor Ln. Suite 204
Costa Mesa, CA 90000

```html
<!DOCTYPE html>
<html lang="en">
<head>
<meta charset="utf-8">
<title>Marcus Dovan, DPM – Business &amp; Appointment Card</title>
<link rel="stylesheet" href="https://fonts.googleapis.com/css2?family=Source+Sans+3:ital,wght@0,400;0,600;0,700;1,400;1,700&display=swap">
<style>
  :root {
    --stage: #111111;
    --card: #ffffff;
    --card-front: #f7f7f8;
    --navy: #1d4a7a;
    --text-grey: #555a60;
    --rule: #7f9fc8;
    --skin-light: #f3d9cb;
    --skin-mid: #e7b9a2;
  }
  * { margin: 0; padding: 0; box-sizing: border-box; }
  html, body { width: 1200px; height: 900px; overflow: hidden; }
  body {
    background: var(--stage);
    font-family: "Source Sans 3", "Myriad Pro", Arial, sans-serif;
    position: relative;
  }
  .card {
    position: absolute;
    top: 170px;
    width: 347px;
    height: 561px;
    background: var(--card);
    overflow: hidden;
  }
  /* Front */
  .card--front { left: 259px; background: var(--card-front); }
  .front__photo {
    height: 255px;
    background:
      radial-gradient(ellipse 55% 45% at 48% 45%, var(--skin-light) 0%, var(--skin-mid) 45%, rgba(231,185,162,0) 75%),
      linear-gradient(180deg, #ffffff 0%, #f7f7f8 100%);
  }
  .front__name {
    margin-top: 14px;
    text-align: center;
    color: var(--navy);
    font-weight: 600;
    font-size: 23px;
    letter-spacing: 0.1px;
  }
  .front__credential, .front__address {
    text-align: center;
    color: var(--text-grey);
    font-size: 15.5px;
    line-height: 19px;
  }
  .front__credential { margin-top: 14px; }
  .front__address { margin-top: 15px; }
  .front__contacts {
    list-style: none;
    margin-top: 22px;
    display: flex;
    flex-direction: column;
    align-items: center;
  }
  .contact {
    display: flex;
    align-items: center;
    gap: 5px;
    color: var(--text-grey);
    font-size: 15.5px;
    line-height: 23px;
  }
  .contact svg { width: 11px; height: 11px; fill: var(--navy); }
  .contact--plain { padding-left: 16px; }

  /* Back */
  .card--back { left: 631px; }
  .back__layout {
    position: absolute;
    left: 0; top: 0;
    width: 561px; height: 347px;
    transform-origin: 0 0;
    transform: translateY(561px) rotate(-90deg);
    color: var(--navy);
  }
  .back__title {
    position: absolute;
    top: 36px; left: 0; width: 561px;
    text-align: center;
    font-weight: 700;
    font-style: italic;
    font-size: 17px;
    letter-spacing: 0.5px;
  }
  .field-line {
    position: absolute;
    left: 56px;
    width: 450px;
    height: 1px;
    background: var(--rule);
  }
  .field-label {
    position: absolute;
    font-size: 15.5px;
    line-height: 18px;
  }
  .back__note {
    position: absolute;
    left: 0; width: 561px;
    text-align: center;
    font-style: italic;
    font-size: 15.5px;
    line-height: 28px;
    top: 230px;
  }
  .back__web {
    position: absolute;
    left: 0; width: 561px;
    text-align: center;
    font-size: 15.5px;
    top: 292px;
  }
</style>
</head>
<body>
  <section class="card card--front">
    <div class="front__photo" role="img" aria-label="Photo of hands gently holding a baby's foot"></div>
    <h1 class="front__name">Marcus Dovan, DPM, Inc.</h1>
    <p class="front__credential">Diplomate, National Council<br>of Lower Limb Medicine</p>
    <p class="front__address">2847 W. Harbor Ln. Suite 204<br>Costa Mesa, CA 90000</p>
    <ul class="front__contacts">
      <li class="contact">
        <svg viewBox="0 0 12 12" aria-hidden="true"><path d="M1 4 Q6 0 11 4 L9.5 5.5 L8 4.5 L8 3.5 Q6 3 4 3.5 L4 4.5 L2.5 5.5 Z M2.5 6.5 L9.5 6.5 L10.5 11 L1.5 11 Z"/></svg>
        1.877.Toes.482
      </li>
      <li class="contact contact--plain">1.555.283.9146</li>
      <li class="contact">
        <svg viewBox="0 0 12 12" aria-hidden="true"><path d="M3 1 H8 V4 H11 V11 H1 V4 H3 Z M4 2 V4 H7 V2 Z M3 6 H5 V7 H3 Z M6 6 H9 V7 H6 Z M3 8 H5 V9 H3 Z M6 8 H9 V9 H6 Z" fill-rule="evenodd"/></svg>
        1.555.671.3820
      </li>
      <li class="contact">
        <svg viewBox="0 0 12 12" aria-hidden="true"><path d="M0.5 2.5 H11.5 V9.5 H0.5 Z M1.5 3.5 L6 6.8 L10.5 3.5 Z" fill-rule="evenodd"/></svg>
        info@DrDovanclinic.example
      </li>
      <li class="contact">
        <svg viewBox="0 0 12 12" aria-hidden="true"><path d="M5 7 L7 5 M4.5 5.5 L2.5 7.5 A1.4 1.4 0 0 0 4.5 9.5 L6.5 7.5 M7.5 6.5 L9.5 4.5 A1.4 1.4 0 0 0 7.5 2.5 L5.5 4.5" fill="none" stroke="#1d4a7a" stroke-width="1.3" stroke-linecap="round"/></svg>
        www.DrDovanclinic.example
      </li>
    </ul>
  </section>

  <section class="card card--back">
    <div class="back__layout">
      <h2 class="back__title">APPOINTMENT</h2>

      <span class="field-label" style="left:56px; top:80px;">For :</span>
      <div class="field-line" style="top:99px;"></div>

      <span class="field-label" style="left:56px; top:120px;">Date :</span>
      <span class="field-label" style="left:266px; top:120px;">Time :</span>
      <div class="field-line" style="top:139px;"></div>

      <span class="field-label" style="left:56px; top:160px;">Location :</span>
      <div class="field-line" style="top:179px;"></div>

      <div class="field-line" style="top:215px;"></div>

      <p class="back__note">If you &nbsp;are unable to keep appointment, please contact<br>us as soon as possible. Call &nbsp;877 555 0148</p>
      <p class="back__web">www.DrDovanclinic.example</p>
    </div>
  </section>
</body>
</html>
```